New Website Design & Build Project - Lively Oak Dishes

I am looking for a professional clean looking website design then build of a website for my meal delivery business Lively Oak Dishes. I already have the domain - www.livelyoakdishes.com.au and I will upload brief for the design and layout of the website.

I have a dropbox full of photos, designs, videos and existing graphic design work that I can share with the designers. This can be provided upon designer request.

I am looking to build this site in WORDPRESS and I would like to build the site using the Velmora Page Composer - https://velmoraskins.example/

Target Market(s)

Kids from 2-16 , Teenagers - 16 - 19, Adults - 19 - 80 + - We Cater For Everyone

Industry/Entity Type

Health And Wellness

Coding

Coded - Design and coding required

Number of Pages Required

5+ page

Colors
33b8a4
abd037
ec1f27
fbee3f
3276b5

Requirements
Must have
• Must incorporate the included Lively Oak Dishes & LOD Logo
Must incorporate designs of packaging into website design.
Must keep text styles consistant throughout design
Must be mobile, tablet and desktop view responsive on all devices.
Must be built in Wordpress
The coder must have experience with velmora skins, velmora page composer, velmora prospects and also be very experienced with setting up products using Quillo Storefront plug in-
https://quillostorefront.example/
I want to integrate Postwren - https://dealbarn.example/postwren/ into site as well
Nice to have
• All of the above
Should not have
• No dark colours

```html
<!DOCTYPE html>
<html lang="en">
<head>
<meta charset="utf-8">
<title>Lively Oak Dishes – Vegan &amp; Vegetarian Meals</title>
<link rel="stylesheet" href="https://fonts.googleapis.com/css2?family=Archivo:wght@600;700;800&family=Lato:wght@400;700&display=swap">
<style>
:root{
  --ink:#1d1d1d;
  --grey-text:#555;
  --green:#21b35f;
  --lime:#8dc63f;
  --footer-lime:#9dcb2c;
  --yellow:#f8ea30;
  --red:#e2001f;
  --white:#ffffff;
  --wood-light:#f1f1f1;
  --wood-dark:#c9c9c9;
}
*{margin:0;padding:0;box-sizing:border-box}
html,body{width:1200px;height:2300px;overflow:hidden;background:var(--white)}
body{position:relative;font-family:"Lato",sans-serif;color:var(--ink)}
.abs{position:absolute}

/* header */
.site-header{position:absolute;left:0;top:0;width:1200px;height:100px;background:var(--white)}
.brand{left:67px;top:32px;display:flex;align-items:center;gap:10px;font-family:"Archivo",sans-serif;font-weight:800;font-size:26px;color:var(--ink);letter-spacing:.5px}
.brand-dot{width:22px;height:22px;border-radius:50%;background:var(--lime)}
.nav a{position:absolute;top:36px;font-family:"Lato",sans-serif;font-weight:700;font-size:16px;color:#6a6a6a;text-decoration:none}
.nav .current{color:var(--ink)}
.member-btn{left:852px;top:23px;width:178px;height:47px;border:2px solid var(--green);color:var(--green);font-weight:700;font-size:16px;display:flex;align-items:center;justify-content:center}
.cart{left:1068px;top:22px}

/* hero */
.hero{left:0;top:100px;width:1200px;height:626px;overflow:hidden;background:linear-gradient(90deg,var(--wood-light),#e3e3e3 60%,var(--wood-dark))}
.hero-title{left:117px;top:166px;font-family:"Archivo",sans-serif;font-weight:800;font-size:58px;line-height:52px;color:var(--ink)}
.hero-sub{left:122px;top:292px;font-family:"Archivo",sans-serif;font-weight:700;font-size:27px;line-height:36px;color:#2a2a2a}
.hero-btn{left:124px;top:385px;width:178px;height:53px;background:var(--lime);color:var(--white);font-family:"Archivo",sans-serif;font-weight:700;font-size:17px;display:flex;align-items:center;justify-content:center}
.dots span{position:absolute;left:1141px;width:13px;height:13px;border-radius:50%;background:var(--white)}
.dots .active{background:transparent;border:2px solid var(--white)}

/* subscription band */
.subscribe{left:0;top:726px;width:1200px;height:165px;background:var(--yellow)}
.subscribe h2{position:absolute;left:133px;top:40px;font-family:"Archivo",sans-serif;font-weight:800;font-size:27px;color:var(--ink)}
.subscribe p{position:absolute;left:133px;top:80px;width:470px;font-size:20px;line-height:21px;color:var(--ink)}
.join-big{left:864px;top:46px;width:179px;height:54px;background:var(--red);color:var(--white);font-family:"Archivo",sans-serif;font-weight:700;font-size:18px;display:flex;align-items:center;justify-content:center}

/* plans */
.plan{top:931px;width:272px;height:211px;color:var(--white);text-align:center}
.plan .photo{position:absolute;inset:0}
.plan .shade{position:absolute;inset:0;background:rgba(0,0,0,.28)}
.plan h3{position:absolute;left:0;right:0;top:74px;font-family:"Archivo",sans-serif;font-weight:700;font-size:18px;line-height:22px}
.plan .price{position:absolute;left:0;right:0;top:122px;font-family:"Archivo",sans-serif;font-weight:800;font-size:36px}
.plan-btn{position:absolute;left:72px;top:188px;width:128px;height:38px;background:var(--red);color:var(--white);font-family:"Archivo",sans-serif;font-weight:700;font-size:13px;display:flex;align-items:center;justify-content:center}

/* article */
.article{left:130px;top:1262px;width:940px;text-align:center}
.article h2{font-family:"Archivo",sans-serif;font-weight:800;font-size:32px;line-height:37px;color:var(--ink);margin-bottom:44px}
.article p{font-size:15.5px;line-height:27px;color:var(--grey-text)}
.article p.gap{margin-top:30px}

/* footer */
.site-footer{left:0;top:2155px;width:1200px;height:145px;background:var(--footer-lime);color:var(--white)}
.footer-links{position:absolute;left:117px;top:45px;display:flex;gap:30px;font-weight:700;font-size:16px;text-transform:uppercase}
.copyright{position:absolute;left:117px;top:75px;font-size:15px}
.social{position:absolute;top:46px;width:44px;height:44px;border:2px solid var(--white);border-radius:50%}
.address{position:absolute;left:916px;top:42px;font-weight:700;font-size:15px;line-height:29px}
.pin{position:absolute;left:884px;top:46px}
</style>
</head>
<body>

<header class="site-header">
  <div class="abs brand"><span class="brand-dot"></span>Lively Oak Dishes</div>
  <nav class="nav">
    <a class="current" style="left:490px">HOME</a>
    <a style="left:594px">CONTACT US</a>
    <a style="left:746px">MENU</a>
  </nav>
  <div class="abs member-btn">MEMBER SIGN UP</div>
  <svg class="abs cart" width="48" height="42" viewBox="0 0 48 42" aria-label="Cart">
    <path d="M2 12h6l5 16h18l4-11H11" fill="none" stroke="#333" stroke-width="2"/>
    <circle cx="15" cy="34" r="2.5" fill="none" stroke="#333" stroke-width="2"/>
    <circle cx="28" cy="34" r="2.5" fill="none" stroke="#333" stroke-width="2"/>
    <circle cx="36" cy="11" r="10" fill="#3cb44a"/>
    <text x="36" y="15" font-family="Lato,sans-serif" font-size="11" font-weight="700" fill="#fff" text-anchor="middle">0</text>
  </svg>
</header>

<section class="abs hero">
  <svg class="abs" style="left:0;top:0" width="1200" height="626" viewBox="0 0 1200 626">
    <path d="M1200 0 L770 0 C760 220 640 520 330 626 L1200 626 Z" fill="#21b35f" role="img" aria-label="Photo of a woman stretching, tinted green"/>
    <circle cx="755" cy="306" r="222" fill="#e7e2d8" role="img" aria-label="Photo of a vegan bowl with beans, corn, capsicum and rice on a white plate"/>
    <circle cx="755" cy="306" r="140" fill="#c8673a" opacity=".55"/>
  </svg>
  <h1 class="abs hero-title">VEGAN &amp;<br>VEGETARIAN</h1>
  <p class="abs hero-sub">HEALTHY MEALS FOOD<br>IN BROOKHAVEN</p>
  <div class="abs hero-btn">VIEW PLANS</div>
  <div class="dots">
    <span class="active" style="top:228px"></span>
    <span style="top:250px"></span>
    <span style="top:272px"></span>
    <span style="top:294px"></span>
  </div>
</section>

<section class="abs subscribe">
  <h2>LIVELY OAK DISHES SUBSCRIPTION SERVICE</h2>
  <p>Join the Lively Oak Dishes subscription service to get the lowest prices. Cancel anytime.</p>
  <div class="abs join-big">JOIN NOW</div>
</section>

<article class="abs plan" style="left:47px">
  <div class="photo" role="img" aria-label="Photo of a child eating a healthy meal" style="background:linear-gradient(135deg,#8a8f94,#5f6d5a)"></div>
  <div class="shade"></div>
  <h3>LOD KIDS 7 DAY<br>MEAL PLAN</h3>
  <div class="price">$35</div>
  <div class="plan-btn">JOIN NOW</div>
</article>
<article class="abs plan" style="left:325px">
  <div class="photo" role="img" aria-label="Photo of adults stretching in a gym" style="background:linear-gradient(135deg,#7a6a58,#4a4038)"></div>
  <div class="shade"></div>
  <h3>LOD ADULT 7 DAY<br>MEAL PLAN</h3>
  <div class="price">$54</div>
  <div class="plan-btn">JOIN NOW</div>
</article>
<article class="abs plan" style="left:604px">
  <div class="photo" role="img" aria-label="Photo of a couple running outdoors on grass" style="background:linear-gradient(135deg,#7f9a55,#56703a)"></div>
  <div class="shade"></div>
  <h3>LOD ADULT 7 DAY<br>COUPLES MEAL PLAN</h3>
  <div class="price">$108</div>
  <div class="plan-btn">JOIN NOW</div>
</article>
<article class="abs plan" style="left:882px">
  <div class="photo" role="img" aria-label="Photo of fresh vegetables and berries on a dark table" style="background:linear-gradient(135deg,#5a4a6a,#3e5a34)"></div>
  <div class="shade"></div>
  <h3>LOD ADULT 21 MEALS<br>PER WEEK PLAN</h3>
  <div class="price">$162</div>
  <div class="plan-btn">JOIN NOW</div>
</article>

<section class="abs article">
  <h2>THE BEST GREEN SMOOTHIE TO<br>START YOUR DAY</h2>
  <p>The King of Green Smoothies would have to be my Superfood Green Smoothie which contains all the elements necessary for unbelievable muscle growth!!! In order to strip off the fat, add lean muscle mass &amp; to provide your body with all the best vitamins &amp; minerals try the following recipe.</p>
  <p>Once you have mixed it up sit back and read on to discover why this green smoothie is going to help you achieve your goals...... Handful of Ice 1 Banana 1 Handful of Organic Kale 1/3 Lemon 3 Dates 1/4 Cup of Water (Or Cocunut Water to make it sweet) 1 1/2 scoops of 100% Whey Protein Powder (Sugar Free is important!!See Supliment Page or Use Egg whites from 6 eggs). 1/4 cup of oats Add either 2 Tablespoons of Pomegranate/Gogi Berries/Acai Berries Teaspoon of Flaxseed Oil As you can see this nutritious smoothie contains a wide variety of proteins, fats , carbohydrates, vitamins &amp; minerals</p>
  <p class="gap">Carbohydrates can be found in breads, pastas, fruit and vegetables and they are important for providing you with energy to get through the day or for the athelete to get through their workout.</p>
  <p class="gap">Slow release carbs such as oatmeal &amp; bran cereal (eaten in the right quantities and at the right times) can actually help you to burn fat!!! The banana and oatmeal that you are consuming in this green smoothie provide you with the perfect amount of carbs to be taken either for breakfast or directly post workout.</p>
  <p class="gap">Protein is needed for muscle tissue repair, building of muscle mass, creating hormones and amino acids while regulating good immune function. Protein is found in meats, fish, tofu, low fat cheese , low fat milk, beans, nuts and legumes. According to the Global Council of Sport Nutrition (GCSN) we require between 1.2 grams and 2.2 grams per kilogram of bodyweight per day for muscle building. This is of course in combination with hard training &amp; surplus calorie consumption. If you do not wish to put on lean muscle aim for about 1/2 this amount. The recommended amount of protein required for muscle growth is found in the above recipe in the form of either 6 egg whites or 1 1/2 .</p>
  <p>The rest of the ingredients such as pomegranate, gogi berries, acai berries and kale and other raw food all contain a plethora of vitamins &amp; minerals necessary for overall health &amp;well being. This green smoothie will give you the absolute best start to the day and I can guarantee you will notice the health</p>
</section>

<footer class="abs site-footer">
  <div class="footer-links"><span>Disclaimer</span><span>Terms &amp; Conditions</span><span>Privacy Policy</span></div>
  <div class="copyright">Copyright – 2020 – Lively Oak Dishes Pty Ltd &nbsp;| ABN – 41 572 903 216</div>
  <span class="social" style="left:748px" aria-label="Social link"></span>
  <span class="social" style="left:800px" aria-label="Social link"></span>
  <svg class="pin" width="24" height="32" viewBox="0 0 24 32" aria-label="Location">
    <path d="M12 1C6 1 1.5 5.5 1.5 11.5 1.5 19 12 31 12 31s10.5-12 10.5-19.5C22.5 5.5 18 1 12 1z" fill="#fff"/>
    <circle cx="12" cy="11.5" r="4" fill="#9dcb2c"/>
  </svg>
  <div class="address">Shop 4 – 27 Wattle Lane,<br>Brookhaven, QLD, 4512</div>
</footer>

</body>
</html>
```